i need a business card for a plumbing company in california

we are a drain cleaning , maintenance plumbing company who is starting new marketing campaign for a tatrench-less pipe installation department .

Target Market(s)

the professional who appreciates time and quality workmanship.

Industry/Entity Type

Plumbing

Colors
0655a3
ec1f27

Requirements
Must have
• the second logo needs to be included
Nice to have
• a focus on the services offered
Should not have
• any underlined words on the brief

```html
<!DOCTYPE html>
<html lang="en">
<head>
<meta charset="utf-8">
<title>Keystone Pipe Works – Business Card</title>
<link href="https://fonts.googleapis.com/css2?family=Open+Sans:wght@300;400;600;700&display=swap" rel="stylesheet">
<style>
  :root {
    --brand-blue: #0655a3;
    --brand-red: #ec1f27;
    --logo-grey: #6b6b63;
    --text-grey: #6f6f6f;
    --paper: #ffffff;
    --backdrop: #d9d9d9;
  }
  * { box-sizing: border-box; margin: 0; padding: 0; }
  html, body { width: 1200px; height: 1200px; overflow: hidden; }
  body {
    background: var(--backdrop);
    font-family: "Open Sans", Arial, sans-serif;
    position: relative;
  }
  .card {
    position: absolute;
    left: 150px;
    width: 900px;
    height: 514px;
    background: var(--paper);
    overflow: hidden;
    box-shadow: 0 8px 24px rgba(0,0,0,0.18);
  }
  .card--back { top: 42px; }
  .card--front { top: 640px; }
  .card__shapes { position: absolute; inset: 0; width: 100%; height: 100%; }
  .logo {
    position: absolute;
    right: 70px;
    top: 60px;
    display: flex;
    align-items: center;
    gap: 12px;
    color: var(--logo-grey);
    font-weight: 700;
    font-size: 34px;
    line-height: 1;
  }
  .logo__mark {
    width: 22px; height: 22px;
    background: var(--brand-red);
    border-radius: 50%;
  }
  /* back side */
  .person {
    position: absolute;
    left: 64px;
    top: 148px;
    color: var(--paper);
  }
  .person__name { font-size: 36px; font-weight: 300; line-height: 1.1; }
  .person__role { font-size: 14px; font-weight: 600; margin-left: 16px; margin-top: 1px; }
  .contacts {
    position: absolute;
    left: 64px;
    top: 232px;
    list-style: none;
    color: var(--paper);
    font-size: 17px;
  }
  .contacts li { display: flex; align-items: center; gap: 16px; height: 40px; }
  .contacts svg { width: 18px; height: 18px; fill: var(--paper); flex: none; }
  .socials {
    position: absolute;
    left: 520px;
    top: 232px;
    list-style: none;
    color: var(--paper);
    font-size: 16px;
  }
  .socials li { display: flex; align-items: center; gap: 16px; height: 40px; }
  .socials__dot { width: 14px; height: 14px; border-radius: 50%; background: var(--paper); flex: none; }
  .services--back {
    position: absolute;
    left: 64px;
    right: 40px;
    top: 418px;
    color: var(--text-grey);
    font-size: 18px;
    line-height: 1.45;
    text-align: center;
  }
  /* front side */
  .tagline {
    position: absolute;
    left: 64px;
    top: 270px;
    color: var(--paper);
    font-size: 34px;
    font-weight: 400;
  }
  .services--front {
    position: absolute;
    left: 64px;
    right: 60px;
    top: 350px;
    color: var(--paper);
    font-size: 24px;
    line-height: 1.5;
  }
  .services strong { font-weight: 700; }
</style>
</head>
<body>

<section class="card card--back" aria-label="Business card back">
  <svg class="card__shapes" viewBox="0 0 900 514" preserveAspectRatio="none" aria-hidden="true">
    <polygon points="0,140 420,140 520,210 0,210" fill="var(--brand-red)"/>
    <rect x="0" y="210" width="900" height="190" fill="var(--brand-blue)"/>
  </svg>
  <div class="logo"><span class="logo__mark"></span>Keystone Pipe Works</div>
  <div class="person">
    <div class="person__name">Marco Delgado</div>
    <div class="person__role">Owner</div>
  </div>
  <ul class="contacts">
    <li><svg viewBox="0 0 24 24"><path d="M6.6 10.8a15.1 15.1 0 0 0 6.6 6.6l2.2-2.2a1 1 0 0 1 1-.25 11.4 11.4 0 0 0 3.6.57 1 1 0 0 1 1 1V20a1 1 0 0 1-1 1A17 17 0 0 1 3 4a1 1 0 0 1 1-1h3.5a1 1 0 0 1 1 1c0 1.25.2 2.45.57 3.6a1 1 0 0 1-.25 1z"/></svg>209-555-0147</li>
    <li><svg viewBox="0 0 24 24"><path d="M2 5h20v14H2zm2 2v.5l8 5 8-5V7zm0 2.8V17h16V9.8l-8 5z"/></svg>hello@keystonepipeworks.com</li>
    <li><svg viewBox="0 0 24 24"><path d="M12 2a10 10 0 1 0 0 20 10 10 0 0 0 0-20zm0 2c.9 0 2.2 1.7 2.8 5H9.2C9.8 5.7 11.1 4 12 4zM4.3 11h2.8a18 18 0 0 0 0 2H4.3a8 8 0 0 1 0-2zm4.8 0h5.8a16 16 0 0 1 0 2H9.1a16 16 0 0 1 0-2zm7.8 0h2.8a8 8 0 0 1 0 2h-2.8a18 18 0 0 0 0-2zM9.2 15h5.6c-.6 3.3-1.9 5-2.8 5s-2.2-1.7-2.8-5z"/></svg>www.keystonepipeworks.com</li>
  </ul>
  <ul class="socials">
    <li><span class="socials__dot"></span>Social: @KeystonePipeWorks</li>
    <li><span class="socials__dot"></span>Video: KeystonePipeWorks</li>
  </ul>
  <p class="services services--back">No-Dig Sewer Line Installs &amp; Repairs - Pipe Lining &amp; Lateral Relining<br>Inspect, Repair, Line Upsizing <strong>DONE IN A DAY</strong></p>
</section>

<section class="card card--front" aria-label="Business card front">
  <svg class="card__shapes" viewBox="0 0 900 514" preserveAspectRatio="none" aria-hidden="true">
    <polygon points="0,255 420,255 520,325 0,325" fill="var(--brand-red)"/>
    <rect x="0" y="325" width="900" height="189" fill="var(--brand-blue)"/>
  </svg>
  <div class="logo"><span class="logo__mark"></span>Keystone Pipe Works</div>
  <div class="tagline">Built On Trust....</div>
  <p class="services services--front">No-Dig Sewer Line Installs &amp; Repairs - Pipe Lining &amp; Lateral Relining Inspect, Repair, Line Upsizing <strong>DONE IN A DAY</strong></p>
</section>

</body>
</html>
```